Animal Eye Clinic needs a Business card

We are a new veterinary ophthalmology practice (Ridgeline Pet Vision Care) and we need a business card designed. We only see animal eyes - we are not a regular veterinary clinic. We already have a logo. We are looking for a professional, good looking business card to hand out to our clients. We are looking for something simple but professional and contemporary. Our logo is likely the only picture/graphic that needs to be on the card.
Updates

Contact Information for Business Card

Delia Vossman, BSc, DVM, MSc, DipACVO
Veterinary Ophthalmologist

Phone: 250.418.3927
Email: ridgelinepetvisioncare@mailbox-example.net
Website: ridgelinepetvisioncare-example.net
Address: 1874 Thornbury Rd
Kelowna, BC, V1X 4M9

Colors

Designer to choose colors to be used in the design.

Requirements
Must have
• Our logo (attached)

```html
<!DOCTYPE html>
<html lang="en">
<head>
<meta charset="utf-8">
<title>Ridgeline Pet Vision Care – Business Card</title>
<link rel="stylesheet" href="https://fonts.googleapis.com/css2?family=Open+Sans:wght@400;600;700&display=swap">
<style>
  :root {
    --teal: #1596a6;
    --teal-faint: #e4f3f6;
    --grey-text: #5f5f5f;
    --grey-label: #7a7a7a;
    --card: #ffffff;
    --backdrop: #dcdcdc;
  }
  * { margin: 0; padding: 0; box-sizing: border-box; }
  html, body { width: 1125px; height: 1200px; overflow: hidden; }
  body {
    background: var(--backdrop);
    font-family: "Open Sans", Arial, sans-serif;
    position: relative;
  }
  .card {
    position: absolute;
    left: 150px;
    width: 825px;
    height: 471px;
    background: var(--card);
    overflow: hidden;
    box-shadow: 0 3px 8px rgba(0,0,0,0.18);
  }
  .card--front { top: 98px; }
  .card--back { top: 630px; }

  /* Front */
  .brand-mark {
    position: absolute;
    left: 44px;
    top: 62px;
    display: flex;
    align-items: center;
    gap: 18px;
  }
  .brand-mark__dot {
    width: 84px; height: 84px;
    border-radius: 50%;
    background: var(--teal);
    flex: none;
  }
  .brand-mark__name {
    color: var(--teal);
    font-weight: 600;
    font-size: 31px;
    line-height: 1.1;
    letter-spacing: 0.5px;
  }
  .backdrop-shape {
    position: absolute;
    left: 390px;
    top: 25px;
    width: 440px;
    height: 440px;
    border-radius: 50%;
    background: var(--teal-faint);
  }
  .person {
    position: absolute;
    left: 44px;
    top: 262px;
  }
  .person__name {
    color: var(--teal);
    font-weight: 700;
    font-size: 19px;
  }
  .person__creds {
    font-size: 14px;
    font-weight: 600;
  }
  .person__title {
    color: var(--grey-label);
    font-weight: 600;
    font-size: 17px;
    margin-top: 2px;
  }
  .address {
    position: absolute;
    left: 44px;
    top: 364px;
    color: var(--grey-text);
    font-size: 16.5px;
    line-height: 23px;
    font-style: normal;
  }
  .divider {
    position: absolute;
    left: 199px;
    top: 357px;
    width: 1px;
    height: 77px;
    background: #bdbdbd;
  }
  .contacts {
    position: absolute;
    left: 219px;
    top: 362px;
    list-style: none;
    color: var(--grey-text);
    font-size: 16.5px;
    line-height: 23px;
  }
  .contacts li { display: flex; align-items: center; gap: 10px; }
  .contacts svg { width: 14px; height: 14px; fill: var(--teal); flex: none; }

  /* Back */
  .back-mark {
    position: absolute;
    left: 0; right: 0;
    top: 128px;
    display: flex;
    justify-content: center;
    align-items: center;
    gap: 22px;
  }
  .back-mark__dot {
    width: 140px; height: 140px;
    border-radius: 50%;
    background: var(--teal);
  }
  .back-mark__name {
    color: var(--teal);
    font-weight: 600;
    font-size: 34px;
    line-height: 1.15;
  }
  .back-url {
    position: absolute;
    left: 0; right: 0;
    top: 404px;
    text-align: center;
    color: var(--grey-text);
    font-size: 17px;
    letter-spacing: 3px;
  }
</style>
</head>
<body>
  <section class="card card--front">
    <div class="backdrop-shape" role="img" aria-label="Faint brand mark decoration"></div>
    <div class="brand-mark">
      <span class="brand-mark__dot"></span>
      <span class="brand-mark__name">Ridgeline Pet<br>Vision Care</span>
    </div>
    <div class="person">
      <p class="person__name">Delia Vossman, <span class="person__creds">BSc, DVM, MSc, DipACVO</span></p>
      <p class="person__title">Veterinary Ophthalmologist</p>
    </div>
    <address class="address">
      1874 Thornbury Rd<br>Kelowna,<br>BC, V1X 4M9
    </address>
    <div class="divider"></div>
    <ul class="contacts">
      <li>
        <svg viewBox="0 0 24 24" aria-hidden="true"><path d="M6.6 10.8a15.1 15.1 0 0 0 6.6 6.6l2.2-2.2a1 1 0 0 1 1-.25 11.4 11.4 0 0 0 3.6.57 1 1 0 0 1 1 1V20a1 1 0 0 1-1 1A17 17 0 0 1 3 4a1 1 0 0 1 1-1h3.5a1 1 0 0 1 1 1c0 1.25.2 2.45.57 3.6a1 1 0 0 1-.25 1z"/></svg>
        250.418.3927
      </li>
      <li>
        <svg viewBox="0 0 24 24" aria-hidden="true"><path d="M2 5h20v14H2z M4 7v.5l8 5 8-5V7l-8 5z" fill-rule="evenodd"/></svg>
        ridgelinepetvisioncare@mailbox-example.net
      </li>
      <li>
        <svg viewBox="0 0 24 24" aria-hidden="true"><circle cx="12" cy="12" r="10"/><path d="M2 12h20M12 2c3 3 3 17 0 20M12 2c-3 3-3 17 0 20" stroke="#fff" stroke-width="1.4" fill="none"/></svg>
        ridgelinepetvisioncare-example.net
      </li>
    </ul>
  </section>

  <section class="card card--back">
    <div class="back-mark">
      <span class="back-mark__dot"></span>
      <span class="back-mark__name">Ridgeline Pet<br>Vision Care</span>
    </div>
    <p class="back-url">www.ridgelinepetvisioncare-example.net</p>
  </section>
</body>
</html>
```